website design Investment Fund

I am looking for a custom website that will work on desktop computer, tablet device and a cellular device. I have attached the booklet so you can get an idea of the look we are going for. Would like to use the website eventually for crowdfunding. We like the ski racer and mountain climbing designs.

Target Market(s)

Financial Services

Industry/Entity Type

Financial Service

Coding

Coded - Design and coding required

Number of Pages Required

5+ page

Font styles to use
Sans Serif

Requirements
Must have
• Must be viewable on a cell phone and tablet and desktop
Nice to have
• Contact us form

```html
<!DOCTYPE html>
<html lang="en">
<head>
<meta charset="utf-8">
<title>Halvern Funding &amp; Investments</title>
<link href="https://fonts.googleapis.com/css2?family=PT+Sans+Narrow:wght@700&family=Montserrat:wght@400;600&display=swap" rel="stylesheet">
<style>
:root{
  --navy:#2a3593;
  --red:#ee1f25;
  --ink:#333;
  --muted:#666;
  --sky:#8fc2ef;
  --snow:#eef3f8;
  --black:#0f0f0f;
  --white:#fff;
}
*{margin:0;padding:0;box-sizing:border-box}
html,body{width:1200px;height:3625px;overflow:hidden}
body{position:relative;background:var(--white);font-family:"Montserrat",sans-serif;color:var(--ink)}
.abs{position:absolute}
.heading{font-family:"PT Sans Narrow",sans-serif;font-weight:700;color:var(--navy);text-transform:uppercase;letter-spacing:.2px}
.copy{font-size:13px;line-height:25px;color:var(--muted)}
.btn{display:flex;align-items:center;justify-content:center;background:var(--red);color:var(--white);text-decoration:none}

.hero-photo{left:0;top:0;width:1200px;height:605px;
  background:linear-gradient(180deg,#7fb6ea 0%,#cfe3f6 22%,#e9f0f7 32%,#a7b8d6 45%,#5d74a8 58%,#c9d3e4 72%,#f3f6fa 86%,#fff 100%)}
.site-header{left:0;top:0;width:1200px;height:100px}
.brand{left:76px;top:38px;display:flex;align-items:center;gap:10px;font-size:24px;font-weight:600;letter-spacing:3px;color:var(--navy)}
.brand-mark{width:14px;height:14px;background:var(--navy)}
.nav{left:636px;top:42px;display:flex;gap:26px;font-size:13px;letter-spacing:.3px}
.nav a{color:#555;text-decoration:none}
.nav a.active{color:var(--navy)}
.hero-title{left:0;top:186px;width:1200px;text-align:center;font-size:58px}

.company-photo{left:100px;top:749px;width:416px;height:416px;border-radius:50%;
  background:radial-gradient(circle at 70% 40%,#f2f07a 0%,#c7d66a 35%,#6f8a4a 70%,#4a5a3a 100%)}
.company-title{left:647px;top:800px;font-size:37px}
.company-copy{left:647px;top:864px;width:478px}
.company-btn{left:649px;top:1066px;width:187px;height:51px;font-family:"PT Sans Narrow",sans-serif;font-weight:700;font-size:20px}

.fund-photo{left:647px;top:1125px;width:553px;height:676px;
  background:radial-gradient(ellipse at 55% 45%,#5f6f86 0%,#9aa8bb 35%,#d5dde7 60%,#fff 85%)}
.fund-title{left:79px;top:1266px;font-size:37px;line-height:44px}
.fund-copy{left:79px;top:1377px;width:575px}
.strategy-title{left:79px;top:1536px;font-size:37px}
.strategy-copy{left:79px;top:1596px;width:575px}

.promise-band{left:0;top:1801px;width:1200px;height:277px;background:var(--navy);display:flex;align-items:center;justify-content:center}
.promise-text{color:var(--white);font-size:34px;line-height:44px;text-align:center}

.accredited-title{left:0;top:2124px;width:1200px;text-align:center;font-size:37px}
.tier{top:2205px;width:500px;height:582px;border:1px solid #d8d8d8;background:var(--white);text-align:center}
.tier-a{left:77px}
.tier-b{left:623px}
.tier-photo{width:100%;height:322px}
.tier-a .tier-photo{background:linear-gradient(180deg,#3f86d6 0%,#a9c9e8 30%,#6b7c98 55%,#dfe6ee 80%,#f4f6f9 100%)}
.tier-b .tier-photo{background:linear-gradient(180deg,#b9c3cc 0%,#8e9ca8 40%,#2f4552 70%,#6f8593 100%)}
.tier-label{margin-top:42px;font-size:18px;font-weight:600;color:#222}
.tier-amount{margin-top:20px;font-size:16px;color:var(--red)}
.tier-rate-label{margin-top:40px;font-size:18px;font-weight:600;color:#222}
.tier-rate{margin-top:18px;font-size:12px;color:var(--muted)}

.cta-photo{left:0;top:2787px;width:1200px;height:431px;
  background:linear-gradient(180deg,#fff 0%,#e3e7eb 25%,#a9b3bc 55%,#d9dee2 75%,#6c7780 100%)}
.cta-title{left:0;top:2950px;width:1200px;text-align:center;font-size:36px;line-height:45px}
.cta-btn{left:506px;top:3064px;width:188px;height:52px;font-size:16px;font-weight:600}

.site-footer{left:0;top:3218px;width:1200px;height:344px;background:var(--black);color:var(--white);text-align:center}
.footer-icon{position:absolute;left:570px;top:70px}
.footer-address{position:absolute;left:0;top:170px;width:1200px;font-size:17px;line-height:29px}
.footer-nav{position:absolute;left:0;top:262px;width:1200px;display:flex;justify-content:center;gap:24px;font-size:13px}
.footer-nav a{color:var(--white);text-decoration:none}
.footer-nav span{color:#aaa}
.legal{left:0;top:3562px;width:1200px;height:63px;background:#050505;color:#ccc;font-size:12px;display:flex;align-items:center;justify-content:center}
</style>
</head>
<body>

<div class="abs hero-photo" role="img" aria-label="Snow-capped mountain range under a blue sky with clouds"></div>
<header class="abs site-header">
  <div class="abs brand"><span class="brand-mark"></span>HALVERN</div>
  <nav class="abs nav">
    <a class="active" href="#">HOME</a><a href="#">ABOUT</a><a href="#">STRATEGY</a><a href="#">INVESTMENT</a><a href="#">NEWS</a><a href="#">CONTACT</a>
  </nav>
</header>
<h1 class="abs heading hero-title">Arizona's Elite Boutique Lender</h1>

<div class="abs company-photo" role="img" aria-label="Hiker with a backpack standing on a rock above misty valleys at sunrise"></div>
<h2 class="abs heading company-title">The Company</h2>
<p class="abs copy company-copy">Halvern Funding &amp; Investment, Inc. is a privately held mortgage lender, asset management and advisory firm headquartered in Mesa Vista, Arizona which specializes in fast financing for debt, equity, mezzanine and land bank on real estate projects in the $100,000 to $50,000,000 range. As a highly reputable, successful and growth-focused company with decades of experience across the entire spectrum of real estate financing through Arizona, the Southwest United States and Mexico.</p>
<a class="abs btn company-btn" href="#">READ MORE</a>

<div class="abs fund-photo" role="img" aria-label="Skier jumping in front of snowy mountain peaks"></div>
<h2 class="abs heading fund-title">The Boutique Fund<br>Investors Are Looking For</h2>
<p class="abs copy fund-copy">As an ELITE BOUTIQUE, full-services, and highly selective firm, we only present our investors deals with highly qualified borrowers and properties with loan to value ratios (LTV) not to exceed 65%-70%. Simply put, we only fund deals with enough equity to allow for a Real Estate market changes. All loans are short terms so we can easily monitor changes in valuation and market conditions.</p>
<h2 class="abs heading strategy-title">Investment Strategy</h2>
<p class="abs copy strategy-copy">The Fund Managers have decades of experience in private money lending as well as real estate investment, property and asset management, construction, and development. In order to produce the desired investor yield, the Fund Managers will utilize their extensive relationships in the marketplace to make a diversified series of investments in secured loans, equity joint ventures, and select value-add estate investments</p>

<section class="abs promise-band">
  <p class="heading promise-text">Totally committed and focused on<br>capital preservation and uninterrupted<br>income for our investors</p>
</section>

<h2 class="abs heading accredited-title">Accredited Investors Only</h2>
<article class="abs tier tier-a">
  <div class="tier-photo" role="img" aria-label="Snowy mountain peaks under a blue sky"></div>
  <p class="tier-label">MINIMUM INVESTMENT REQUIREMENTS</p>
  <p class="tier-amount">SERIES A $50,000-$249,999</p>
  <p class="tier-rate-label">RATE OF RETURN</p>
  <p class="tier-rate">SERIES A 7% PER ANNUM (Term 24 months)</p>
</article>
<article class="abs tier tier-b">
  <div class="tier-photo" role="img" aria-label="Misty pine forest on a hillside"></div>
  <p class="tier-label">MINIMUM INVESTMENT REQUIREMENTS</p>
  <p class="tier-amount">SERIES B $250,000.00</p>
  <p class="tier-rate-label">RATE OF RETURN</p>
  <p class="tier-rate">SERIES B 8% PER ANNUM (Term 24 months)</p>
</article>

<div class="abs cta-photo" role="img" aria-label="Fog drifting over forested mountain slopes"></div>
<h2 class="abs heading cta-title">Your Elite Boutique<br>Lender, Where Creativity Counts</h2>
<a class="abs btn cta-btn" href="#">CONTACT US</a>

<footer class="abs site-footer">
  <svg class="footer-icon" width="60" height="70" viewBox="0 0 60 70" fill="none" stroke="#fff" stroke-width="2">
    <path d="M30 4a12 12 0 0 1 12 12c0 9-12 22-12 22S18 25 18 16A12 12 0 0 1 30 4z"/>
    <circle cx="30" cy="16" r="4"/>
    <path d="M4 36l14-6 14 6 14-6 10 4v32l-10-4-14 6-14-6-14 6z"/>
    <path d="M18 30v32M32 36v32M46 30v32"/>
  </svg>
  <p class="footer-address">2280 N. Canyon Ridge Drive Suite<br>9 Mesa Vista, AZ 85000</p>
  <nav class="footer-nav">
    <a href="#">Home</a><span>|</span><a href="#">Strategy</a><span>|</span><a href="#">Investment</a><span>|</span><a href="#">News</a><span>|</span><a href="#">Contact</a>
  </nav>
</footer>
<div class="abs legal">©HALVERN- 2019. All Rights Reserved.</div>

</body>
</html>
```